Meridale Staffing Website

My business has been word of mouth over the last 3 years and has grown. Now I need a website for additional marketing as we have new clients asking for a website.

You have already completed my Logo during an earlier project. I have attached the logo.

We do Staff Augmentation and Operation Support.

What is that?
Staff augmentation is an outsourcing strategy that allows companies to fill specific, temporary roles to achieve business objectives. This staffing method complements existing teams with specific talent, enhancing business capabilities or filling gaps left by members on extended leave.

We work alongside the internal recruiting team to assist clients to meet and exceed financial goals.

```html
<!DOCTYPE html>
<html lang="en">
<head>
<meta charset="utf-8">
<title>Meridale Staffing</title>
<link rel="stylesheet" href="https://fonts.googleapis.com/css2?family=Oswald:wght@600;700&family=Raleway:ital,wght@0,400;0,500;0,600;0,700;1,400&display=swap">
<style>
:root{
  --navy:#0e5581;
  --navy-deep:#134a70;
  --ink:#333a40;
  --muted:#5c646b;
  --grey:#8c8f92;
  --pale:#eef8fc;
  --white:#ffffff;
  --black:#050607;
  --field:#d9e2e8;
}
*{box-sizing:border-box;margin:0;padding:0}
html,body{width:1200px;height:3901px;overflow:hidden}
body{position:relative;font-family:"Raleway",sans-serif;color:var(--ink);background:var(--white)}
.abs{position:absolute}
.btn{position:absolute;display:flex;align-items:center;justify-content:center;background:var(--navy);color:var(--white);font-weight:600;font-size:15px;border-radius:7px;letter-spacing:.3px}
.btn--ghost{background:transparent;border:1.5px solid var(--white)}
.eyebrow{position:absolute;width:100%;text-align:center;font-size:14px;color:var(--ink)}
.section-title{position:absolute;width:100%;text-align:center;font-size:31px;font-weight:600;color:var(--navy);letter-spacing:.3px;line-height:38px}

/* header */
.site-header{position:absolute;left:0;top:0;width:1200px;height:75px;background:var(--white)}
.brand{position:absolute;display:flex;align-items:center;gap:10px}
.brand__mark{width:34px;height:34px;border-radius:50%;background:var(--navy)}
.brand__name{font-weight:700;font-size:22px;color:var(--navy);line-height:1;white-space:nowrap}
.nav a{position:absolute;top:31px;font-size:11.5px;color:var(--ink);text-decoration:none;letter-spacing:.2px}
.nav a.is-active{color:var(--navy)}
.nav a.is-active::after{content:"";position:absolute;left:0;right:0;top:22px;height:2px;background:var(--navy)}

/* hero */
.hero{position:absolute;left:0;top:75px;width:1200px;height:640px;overflow:hidden}
.hero__photo{position:absolute;inset:0;background:linear-gradient(180deg,#4a4f55 0%,#6d6a66 40%,#3d3e42 100%)}
.hero__shade{position:absolute;inset:0;background:rgba(10,20,30,.25)}
.hero__line1{position:absolute;top:240px;width:100%;text-align:center;font-family:"Oswald",sans-serif;font-weight:700;font-size:44px;color:var(--white);letter-spacing:.5px}
.hero__band{position:absolute;left:300px;top:300px;width:600px;height:59px;background:var(--navy);display:flex;align-items:center;justify-content:center;font-family:"Oswald",sans-serif;font-weight:700;font-size:44px;color:var(--white);letter-spacing:.5px}
.hero__sub{position:absolute;top:373px;width:100%;text-align:center;font-size:16px;color:var(--white)}
.hero__dots span{position:absolute;left:1130px;width:4px;height:4px;border-radius:50%;background:var(--white)}

/* about */
.about__art{position:absolute;left:155px;top:755px;width:370px;height:453px;border-radius:8px;background:linear-gradient(135deg,#0e5581 0%,#c99a88 55%,#8a8a8a 100%)}
.about__kicker{position:absolute;left:632px;top:832px;font-size:13px}
.about__title{position:absolute;left:631px;top:860px;font-size:31px;font-weight:600;color:var(--navy);line-height:37px}
.about__text{position:absolute;left:634px;width:330px;font-size:11.5px;line-height:21px;color:var(--muted)}

/* services */
.service{position:absolute;overflow:hidden}
.service--staff{left:0;top:1340px;width:600px;height:350px;background:var(--navy-deep)}
.service--ops{left:600px;top:1289px;width:600px;height:348px;background:#7b7e81}
.service__photo{position:absolute;inset:0}
.service__icon{position:absolute;width:83px;height:83px;border-radius:50%;background:var(--white)}
.service__title{position:absolute;font-size:22px;font-weight:500;color:var(--white);letter-spacing:.3px}
.service__text{position:absolute;width:340px;font-size:11.5px;line-height:19.5px;color:var(--white)}

/* how it works */
.how{position:absolute;left:0;top:1690px;width:1200px;height:542px;background:var(--pale)}
.how__sub{position:absolute;left:0;top:1868px;width:1200px;text-align:center;font-size:12.5px;line-height:21px;color:var(--ink)}
.how__team{position:absolute;left:178px;top:1955px;width:842px;height:277px;background:linear-gradient(180deg,#c9ced3 0%,#5e6670 55%,#2b3440 100%)}
.how__rule{position:absolute;left:112px;top:2230px;width:975px;height:3px;background:var(--navy)}

/* trust */
.badge{position:absolute;top:2430px;width:90px;height:90px}

/* testimonial */
.reviews{position:absolute;left:0;top:2596px;width:1200px;height:427px;background:linear-gradient(90deg,#1b5c86,#2a6c94 50%,#1b5c86)}
.reviews__title{position:absolute;top:80px;width:100%;text-align:center;font-size:31px;font-weight:500;color:var(--white)}
.reviews__avatar{position:absolute;left:553px;top:137px;width:94px;height:94px;border-radius:50%;border:3px solid var(--white);background:linear-gradient(160deg,#e8b68c,#b5734a)}
.reviews__arrow{position:absolute;top:204px;width:60px;height:32px;border:1.5px solid var(--white);border-radius:16px}
.reviews__quote{position:absolute;left:330px;top:254px;width:540px;text-align:center;font-style:italic;font-size:12.5px;line-height:21px;color:var(--white)}
.reviews__name{position:absolute;top:340px;width:100%;text-align:center;font-size:13px;font-weight:600;color:var(--white);letter-spacing:.5px}

/* contact */
.contact__photo{position:absolute;left:205px;top:3165px;width:320px;height:475px;background:linear-gradient(180deg,#f4f2ef 0%,#d8d3ce 60%,#9c8f86 100%);border-radius:160px 160px 0 0}
.field{position:absolute;left:601px;width:435px;height:36px;border:1px solid var(--field);border-radius:6px;background:var(--white);font-size:11px;color:var(--muted);padding:11px 14px}
.field--area{height:82px}

/* footer */
.footer{position:absolute;left:0;top:3560px;width:1200px;height:341px}
.footer__col-title{position:absolute;top:3655px;font-size:13.5px;font-weight:500;color:var(--navy);letter-spacing:.4px}
.footer__list li{position:absolute;list-style:none;font-size:12px;color:#d4d8db;padding-left:18px}
.footer__list li::before{content:"";position:absolute;left:0;top:5px;width:5px;height:5px;border-radius:50%;background:var(--navy)}
.footer__contact{position:absolute;left:935px;font-size:12px;line-height:19px;color:#d4d8db;width:220px}
.footer__icon{position:absolute;left:888px;width:34px;height:34px;border-radius:50%;background:var(--navy)}
.social{position:absolute;top:3774px;width:36px;height:36px;border-radius:50%;background:var(--navy)}
.footer__rule{position:absolute;left:62px;top:3855px;width:1076px;height:1px;background:#2a2f34}
.footer__copy{position:absolute;top:3875px;width:100%;text-align:center;font-size:11px;color:#cfd3d6}
.footer__copy span{color:var(--navy)}
</style>
</head>
<body>

<header class="site-header">
  <div class="brand" style="left:58px;top:20px">
    <span class="brand__mark"></span>
    <span class="brand__name">MERIDALE STAFFING</span>
  </div>
  <nav class="nav">
    <a class="is-active" href="#" style="left:602px">HOME</a>
    <a href="#" style="left:663px">SERVICES</a>
    <a href="#" style="left:738px">ABOUT US</a>
    <a href="#" style="left:817px">OUR WORKS</a>
    <a href="#" style="left:908px">CAREER</a>
  </nav>
  <svg class="abs" style="left:975px;top:30px" width="16" height="16" viewBox="0 0 16 16"><circle cx="6.5" cy="6.5" r="5" fill="none" stroke="#333a40" stroke-width="1.8"/><line x1="10.5" y1="10.5" x2="15" y2="15" stroke="#333a40" stroke-width="1.8"/></svg>
  <div class="btn" style="left:1012px;top:20px;width:128px;height:36px;font-size:14px">CONTACT US</div>
</header>

<section class="hero">
  <div class="hero__photo" role="img" aria-label="Team of smiling office colleagues giving thumbs up"></div>
  <div class="hero__shade"></div>
  <div class="hero__line1">FIND A PERFECT</div>
  <div class="hero__band">CANDIDATE FOR YOUR PROJECTS</div>
  <div class="hero__sub">We do Staff Augmentation and Operation Support.</div>
  <div class="hero__dots">
    <svg class="abs" style="left:1125px;top:208px" width="14" height="14"><circle cx="7" cy="7" r="5" fill="none" stroke="#6fa7cc" stroke-width="1.5"/></svg>
    <span style="top:230px;height:40px;width:1px;left:1132px;border-radius:0;background:rgba(255,255,255,.6)"></span>
    <span style="top:272px"></span><span style="top:287px"></span><span style="top:302px"></span><span style="top:317px"></span>
  </div>
  <svg class="abs" style="left:0;top:0" width="1200" height="640" viewBox="0 0 1200 640">
    <path d="M0 560 Q120 590 205 600 Q170 560 150 500 Q230 620 520 630 Q900 640 1200 548 L1200 640 L0 640 Z" fill="#fff"/>
    <path d="M205 600 Q165 570 150 500" fill="none" stroke="#0e5581" stroke-width="2"/>
    <path d="M520 630 Q900 640 1200 548" fill="none" stroke="#0e5581" stroke-width="2"/>
    <rect x="590" y="550" width="20" height="30" rx="10" fill="none" stroke="#fff" stroke-width="1.6"/>
    <line x1="600" y1="557" x2="600" y2="564" stroke="#fff" stroke-width="1.6"/>
    <path d="M594 585 L600 591 L606 585" fill="none" stroke="#fff" stroke-width="1.6"/>
  </svg>
</section>
<div class="abs" style="left:600px;top:670px;width:1px;height:75px;background:var(--navy)"></div>

<section class="about">
  <div class="about__art" role="img" aria-label="Illustration of hands exchanging a resume inside a circular arrow, with candidate profile photos"></div>
  <div class="about__kicker">What Is That?</div>
  <div class="about__title">MERIDALE<br>STAFFING</div>
  <p class="about__text" style="top:950px">Staff augmentation is an outsourcing strategy that allows companies to fill specific, temporary roles to achieve business objectives.</p>
  <p class="about__text" style="top:1026px">This staffing method complements existing teams with specific talent, enhancing business capabilities or filling gaps left by members on extended leave.</p>
  <div class="btn" style="left:634px;top:1110px;width:142px;height:42px">LEARN MORE</div>
</section>

<section class="service service--staff">
  <div class="service__photo" role="img" aria-label="Team working in an office, tinted blue" style="background:linear-gradient(90deg,rgba(19,74,112,.9),rgba(30,90,130,.85))"></div>
  <span class="service__icon" style="left:68px;top:87px"></span>
  <div class="service__title" style="left:171px;top:93px">STAFF AUGMENTATION</div>
  <p class="service__text" style="left:171px;top:120px">Lorem ipsum has been the industry's standard dummy text ever since then, when an unknown printer took a galley of type and scrambled it to make a type specimen book. It has survived not only five centuries...</p>
  <div class="btn btn--ghost" style="left:171px;top:217px;width:142px;height:42px">LEARN MORE</div>
</section>

<section class="service service--ops">
  <div class="service__photo" role="img" aria-label="Open plan office interior, tinted grey" style="background:linear-gradient(90deg,#777a7d,#8d9092)"></div>
  <span class="service__icon" style="left:60px;top:73px"></span>
  <svg class="abs" style="left:80px;top:93px" width="44" height="44" viewBox="0 0 44 44" fill="none" stroke="#0e5581" stroke-width="2"><rect x="14" y="2" width="16" height="14" rx="2"/><rect x="2" y="26" width="12" height="14" rx="2"/><rect x="16" y="26" width="12" height="14" rx="2"/><rect x="30" y="26" width="12" height="14" rx="2"/><path d="M22 16 V22 M8 22 H36 M8 22 V26 M22 22 V26 M36 22 V26"/></svg>
  <div class="service__title" style="left:166px;top:70px">OPERATION SUPPORT</div>
  <p class="service__text" style="left:166px;top:108px">Lorem Ipsum has been the industry's standard dummy text ever since then, when an unknown printer took a galley of type and scrambled it to make a type specimen book. It has survived not only five centuries...</p>
  <div class="btn" style="left:166px;top:204px;width:142px;height:42px">LEARN MORE</div>
</section>

<section class="how"></section>
<h2 class="section-title" style="top:1777px">HOW STAFF<br>AUGMENTATION WORKS</h2>
<p class="how__sub">If you love solving problems, thrive in a team environment, and see the<br>world as filled with opportunities, consider joining us.</p>
<div class="how__team" role="img" aria-label="Group of business professionals standing together"></div>
<div class="how__rule"></div>
<div class="btn" style="left:469px;top:2198px;width:262px;height:67px;font-size:17px;border-radius:10px">VIEW OPEN POSITIONS</div>

<section class="trust">
  <div class="eyebrow" style="top:2340px">Our Works</div>
  <h2 class="section-title" style="top:2362px">WE ARE A TRUSTED PARTNER</h2>
  <svg class="badge" style="left:328px" viewBox="0 0 90 90"><polygon points="45,3 84,24 84,66 45,87 6,66 6,24" fill="#fff" stroke="#4a5157" stroke-width="2"/><rect x="10" y="38" width="70" height="14" fill="#1f2a33"/></svg>
  <svg class="badge" style="left:448px" viewBox="0 0 90 90"><polygon points="45,3 84,24 84,66 45,87 6,66 6,24" fill="#fff" stroke="#4a5157" stroke-width="2"/><rect x="10" y="38" width="70" height="14" fill="#1f2a33"/></svg>
  <svg class="badge" style="left:559px" viewBox="0 0 90 90"><circle cx="45" cy="45" r="42" fill="#fff" stroke="#1e3a6d" stroke-width="3"/><circle cx="45" cy="45" r="34" fill="none" stroke="#1e3a6d" stroke-width="1"/></svg>
  <svg class="badge" style="left:670px" viewBox="0 0 90 90"><polygon points="45,3 84,24 84,66 45,87 6,66 6,24" fill="#fff" stroke="#4a5157" stroke-width="2"/><rect x="10" y="38" width="70" height="14" fill="#1f2a33"/></svg>
  <svg class="badge" style="left:785px" viewBox="0 0 90 90"><polygon points="45,3 84,24 84,66 45,87 6,66 6,24" fill="#fff" stroke="#4a5157" stroke-width="2"/><rect x="10" y="38" width="70" height="14" fill="#1f2a33"/></svg>
</section>

<section class="reviews" role="img" aria-label="Office with plant, tinted blue">
  <div class="reviews__title">WHAT OUR CLIENT SAY</div>
  <div class="reviews__avatar" role="img" aria-label="Client portrait"></div>
  <div class="reviews__arrow" style="left:98px"><svg width="60" height="32"><path d="M42 16 H18 M24 10 L18 16 L24 22" fill="none" stroke="#fff" stroke-width="1.5"/></svg></div>
  <div class="reviews__arrow" style="left:1042px"><svg width="60" height="32"><path d="M18 16 H42 M36 10 L42 16 L36 22" fill="none" stroke="#fff" stroke-width="1.5"/></svg></div>
  <p class="reviews__quote">" Lorem Ipsum has been the industry's standard dummy text ever since the 1500s, when an unknown printer took a galley of type and scrambled it to make a type specimen book. It has survived not only five centuries, but also the leap "</p>
  <div class="reviews__name">— &nbsp;CLIENT NAME</div>
</section>

<section class="contact">
  <div class="eyebrow" style="top:3097px">Contact Us</div>
  <h2 class="section-title" style="top:3125px">GET IN TOUCH WITH US</h2>
  <div class="contact__photo" role="img" aria-label="Woman with glasses holding a phone and a cup of tea"></div>
  <div class="field" style="top:3206px">Name *</div>
  <div class="field" style="top:3251px">Email *</div>
  <div class="field" style="top:3296px">Phone *</div>
  <div class="field field--area" style="top:3341px">Message *</div>
  <div class="btn" style="left:601px;top:3437px;width:105px;height:40px">SUBMIT</div>
</section>

<footer class="footer">
  <svg class="abs" style="left:0;top:0" width="1200" height="341" viewBox="0 0 1200 341">
    <path d="M0 125 Q400 20 1200 5 L1200 341 L0 341 Z" fill="#050607"/>
    <path d="M0 118 Q380 25 1200 0 L1200 20 Q420 40 0 125 Z" fill="#0e5581"/>
  </svg>
</footer>
<div class="brand" style="left:78px;top:3712px">
  <span class="brand__mark" style="width:36px;height:36px"></span>
  <span class="brand__name" style="font-size:18px">MERIDALE STAFFING</span>
</div>
<span class="social" style="left:129px"></span>
<span class="social" style="left:171px"></span>
<span class="social" style="left:213px"></span>

<div class="footer__col-title" style="left:337px">SITEMAP</div>
<ul class="footer__list">
  <li style="left:337px;top:3690px">Home</li>
  <li style="left:337px;top:3716px">Services</li>
  <li style="left:337px;top:3743px">About Us</li>
  <li style="left:337px;top:3769px">Our Works</li>
  <li style="left:337px;top:3795px">Career</li>
</ul>
<div class="footer__col-title" style="left:612px">WHAT WE DO</div>
<ul class="footer__list">
  <li style="left:612px;top:3690px">Staff Augmentation</li>
  <li style="left:612px;top:3716px">Operation Support</li>
</ul>
<div class="footer__col-title" style="left:889px">CONTACT US</div>
<span class="footer__icon" style="top:3688px"></span>
<svg class="abs" style="left:898px;top:3696px" width="14" height="18" viewBox="0 0 14 18"><path d="M7 17 C2 11 1 8 1 6 A6 6 0 0 1 13 6 C13 8 12 11 7 17 Z" fill="none" stroke="#fff" stroke-width="1.5"/><circle cx="7" cy="6" r="2" fill="#fff"/></svg>
<div class="footer__contact" style="top:3687px">Meridale Staffing, LLC<br>101 - lorem ipsum simple text print type settting industry</div>
<span class="footer__icon" style="top:3763px"></span>
<svg class="abs" style="left:897px;top:3772px" width="16" height="16" viewBox="0 0 16 16"><path d="M3 1 L6 1 L7 5 L5 6.5 Q6.5 9.5 9.5 11 L11 9 L15 10 L15 13 Q15 15 13 15 Q1 14 1 3 Q1 1 3 1 Z" fill="#fff"/></svg>
<div class="footer__contact" style="top:3771px;font-size:14px">123 456 7890</div>
<span class="footer__icon" style="top:3806px"></span>
<svg class="abs" style="left:897px;top:3817px" width="16" height="12" viewBox="0 0 16 12"><rect x="0.5" y="0.5" width="15" height="11" rx="1.5" fill="#fff"/><path d="M1 1 L8 7 L15 1" fill="none" stroke="#0e5581" stroke-width="1.3"/></svg>
<div class="footer__contact" style="top:3815px">info@meridalestaffing.com</div>
<div class="footer__rule"></div>
<div class="footer__copy">©2022 <span>MERIDALE STAFFING, LLC</span> ~ 2021 All rights reserved.</div>

</body>
</html>
```